Veldmark Supplies Business Card

Professional business card that stand out to our potential customers. Front and back with clean modern design

Industry/Entity Type

Oil and gas

Contact Information for Business Card

Name, address, website , office phone and cell number

Requirements
Must have
• Editable files for each employee

```html
<!DOCTYPE html>
<html lang="en">
<head>
<meta charset="utf-8">
<title>Veldmark Supplies – Business Card</title>
<link href="https://fonts.googleapis.com/css2?family=Montserrat:wght@400;500;800&display=swap" rel="stylesheet">
<style>
  :root {
    --backdrop: #3b3b3c;
    --card: #2b2b2d;
    --red: #e21f26;
    --blue: #1fb1d4;
    --white: #ffffff;
    --muted: #e8e8e8;
  }
  * { box-sizing: border-box; margin: 0; padding: 0; }
  html, body {
    width: 1200px; height: 689px; overflow: hidden;
    background: var(--backdrop);
    font-family: "Montserrat", sans-serif;
  }
  .stage {
    width: 1200px; height: 689px;
    display: flex; align-items: center; justify-content: center; gap: 50px;
  }
  .card {
    width: 530px; height: 304px;
    background: var(--card);
    border-radius: 18px;
    position: relative;
    overflow: hidden;
  }
  /* front */
  .card-front {
    display: flex; align-items: center; justify-content: center;
  }
  .brand {
    display: flex; align-items: center; gap: 14px;
  }
  .brand-square {
    width: 34px; height: 34px; background: var(--red);
  }
  .brand-name {
    font-weight: 800; color: var(--white);
    text-transform: uppercase; letter-spacing: 2px;
    font-size: 30px; line-height: 1;
  }
  /* back */
  .card-back { display: flex; }
  .back-brand {
    width: 230px; display: flex; align-items: center; justify-content: center;
  }
  .back-brand .brand-square { width: 20px; height: 20px; }
  .back-brand .brand-name { font-size: 17px; letter-spacing: 1.2px; }
  .divider {
    width: 24px; position: relative;
  }
  .divider span {
    position: absolute; top: 40px; bottom: 40px; width: 2px;
  }
  .divider .line-blue { left: 6px; background: var(--blue); }
  .divider .line-red { left: 14px; top: 70px; bottom: 60px; background: var(--red); }
  .contact {
    flex: 1; padding: 44px 24px 30px 22px; color: var(--muted);
  }
  .person-name {
    color: var(--red); font-weight: 800; font-size: 22px;
    text-transform: uppercase; letter-spacing: .5px;
  }
  .person-title { font-size: 13px; margin-top: 2px; }
  .address { font-size: 12.5px; line-height: 1.35; margin-top: 12px; }
  .details { list-style: none; margin-top: 12px; }
  .details li {
    display: flex; align-items: center; gap: 9px;
    font-size: 12.5px; line-height: 1; margin-bottom: 7px;
  }
  .icon {
    width: 16px; height: 16px; background: var(--red);
    display: flex; align-items: center; justify-content: center; flex: none;
  }
  .icon svg { width: 11px; height: 11px; }
</style>
</head>
<body>
<main class="stage">
  <section class="card card-front" aria-label="Card front">
    <div class="brand">
      <span class="brand-square"></span>
      <span class="brand-name">Veldmark Supplies</span>
    </div>
  </section>

  <section class="card card-back" aria-label="Card back">
    <div class="back-brand">
      <div class="brand">
        <span class="brand-square"></span>
        <span class="brand-name">Veldmark Supplies</span>
      </div>
    </div>
    <div class="divider" aria-hidden="true">
      <span class="line-blue"></span>
      <span class="line-red"></span>
    </div>
    <div class="contact">
      <h1 class="person-name">Dale Harwick</h1>
      <p class="person-title">President</p>
      <p class="address">4820 Ridgeline Rd, Ste<br>200, Midland, TX 79705</p>
      <ul class="details">
        <li>
          <span class="icon"><svg viewBox="0 0 12 12"><path fill="#fff" d="M2.5 1h2l1 2.5-1.2 1a6 6 0 0 0 3.2 3.2l1-1.2L11 7.5v2c0 .8-.7 1.5-1.5 1.5A8.5 8.5 0 0 1 1 2.5C1 1.7 1.7 1 2.5 1z"/></svg></span>
          432-555-0148
        </li>
        <li>
          <span class="icon"><svg viewBox="0 0 12 12"><rect x="3" y="0.5" width="6" height="11" rx="1" fill="none" stroke="#fff" stroke-width="1.2"/><circle cx="6" cy="9.5" r=".7" fill="#fff"/></svg></span>
          000-000-9999
        </li>
        <li>
          <span class="icon"><svg viewBox="0 0 12 12"><rect x="1" y="2.5" width="10" height="7" fill="none" stroke="#fff" stroke-width="1.1"/><path d="M1 2.5l5 4 5-4" fill="none" stroke="#fff" stroke-width="1.1"/></svg></span>
          info@example-youremail.com
        </li>
        <li>
          <span class="icon"><svg viewBox="0 0 12 12"><circle cx="6" cy="6" r="5" fill="none" stroke="#fff" stroke-width="1.1"/><path d="M1 6h10M6 1c2 2.5 2 7.5 0 10M6 1c-2 2.5-2 7.5 0 10" fill="none" stroke="#fff" stroke-width=".9"/></svg></span>
          www.example-yourwebsite.com
        </li>
      </ul>
    </div>
  </section>
</main>
</body>
</html>
```